Resposive web site in 4 languages + image gallery + logo design

We need a web page, which will work on all devices.
I have uploaded web page concept.
Company name: Praxelun
Industry/Entity Type
It Company
Logo Text
quality matters
Coding
Coded - Design and coding required
Number of Pages Required
1 page

```html
<!DOCTYPE html>
<html lang="en">
<head>
<meta charset="utf-8">
<title>Praxelun — Woodworks, Stoneworks, Restoration</title>
<link href="https://fonts.googleapis.com/css2?family=Montserrat:wght@400;500;600&family=Open+Sans:wght@400;600&family=Dosis:wght@400;500&display=swap" rel="stylesheet">
<style>
:root{
  --red:#e00d0d;
  --ink:#222222;
  --text:#444444;
  --muted:#777777;
  --line:#dddddd;
  --dark:#1c1c1c;
  --footer:#1e1e1e;
  --panel:#f0f0f0;
  --white:#ffffff;
}
*{margin:0;padding:0;box-sizing:border-box}
html,body{width:1200px;height:2830px;overflow:hidden}
body{position:relative;background:var(--white);font-family:"Open Sans",Arial,sans-serif;color:var(--text)}
.abs{position:absolute}

/* hero */
.hero-photo{left:0;top:0;width:1200px;height:670px;background:radial-gradient(ellipse at 62% 40%,#c59a5c 0%,#7a5530 35%,#3a2615 70%,#1c130b 100%)}
.topbar{left:0;top:0;width:1200px;height:98px;background:rgba(0,0,0,.55)}
.logo{left:100px;top:26px;font-family:"Montserrat",sans-serif;font-size:33px;font-weight:500;color:var(--white)}
.nav{top:40px;font-family:"Montserrat",sans-serif;font-size:11px;font-weight:500;color:var(--white);letter-spacing:.3px}
.nav.active{color:var(--red)}
.nav-divider{top:34px;width:1px;height:32px;background:rgba(255,255,255,.5)}
.lang{left:887px;top:40px;font-size:11px;color:var(--white);font-family:"Montserrat",sans-serif}
.lang svg{vertical-align:middle;margin-left:8px}
.social-top{left:1067px;top:34px;width:32px;height:32px;border-radius:50%;background:#2a63d6}
.hero-label{left:100px;top:534px;width:321px;height:59px;background:rgba(40,40,40,.75);color:var(--white);font-family:"Montserrat",sans-serif;font-size:32px;font-weight:500;letter-spacing:1px;padding:10px 0 0 32px}
.dots{left:578px;top:644px;display:flex;gap:8px}
.dots span{width:6px;height:6px;border-radius:50%;background:rgba(255,255,255,.5)}
.dots span:first-child{background:var(--white)}

/* quote band */
.quote-band{left:0;top:670px;width:1200px;height:96px;background:var(--red)}
.quote-text{left:258px;top:706px;font-family:"Montserrat",sans-serif;font-size:21px;font-weight:500;color:var(--white)}
.quote-btn{left:647px;top:696px;width:251px;height:44px;background:#262626;color:var(--white);font-family:"Montserrat",sans-serif;font-size:21px;font-weight:500;text-align:center;line-height:44px}

/* services */
.section-title{width:1200px;left:0;text-align:center;font-family:"Montserrat",sans-serif;font-size:30px;font-weight:500;color:var(--ink);letter-spacing:.5px}
.service-photo{width:289px;height:250px;border-radius:3px}
.ph-wood{background:linear-gradient(135deg,#4a3220,#a87a45 55%,#3a2616)}
.ph-stone{background:linear-gradient(135deg,#6e6a66,#b9b4ab 50%,#55524f)}
.ph-restore{background:linear-gradient(135deg,#3d2b1e,#8e6b4e 50%,#2d2017)}
.service-name{font-family:"Montserrat",sans-serif;font-size:20px;font-weight:500;color:var(--ink)}
.service-copy{width:640px;font-size:13px;line-height:21px;color:var(--text)}
.tags{font-size:13px;color:var(--text);word-spacing:2px}
.tags span{margin-right:16px}
.btn{height:40px;width:113px;font-size:13px;color:var(--white);text-align:center;line-height:40px;border-radius:2px}
.btn-red{background:var(--red)}
.btn-dark{background:#262626}
.rule{left:100px;width:1002px;height:1px;background:var(--line)}

/* about */
.about-band{left:0;top:1881px;width:1200px;height:378px;background:linear-gradient(90deg,#151515,#2a2622 50%,#161616)}
.about-photo{left:98px;top:1947px;width:347px;height:248px;background:linear-gradient(135deg,#c9c7c2,#8a8077 55%,#e3e1dc)}
.about-title{left:485px;top:1940px;font-family:"Montserrat",sans-serif;font-size:32px;font-weight:500;color:var(--white)}
.about-copy{left:483px;top:2002px;width:590px;font-size:13.5px;line-height:22px;color:#e8e8e8}
.about-sign{left:492px;top:2167px;font-size:13.5px;color:#e8e8e8}
.about-sign b{font-weight:600;color:var(--white)}

/* contact */
.contact-sub{width:1200px;left:0;top:2390px;text-align:center;font-size:14px;font-weight:600;color:var(--ink)}
.info-label{left:185px;font-family:"Dosis",sans-serif;font-size:16px;letter-spacing:2px;color:#555}
.info-value{left:185px;font-family:"Dosis",sans-serif;font-size:14px;line-height:22px;color:var(--ink)}
.form-panel{left:443px;top:2461px;width:574px;height:241px;background:var(--panel)}
.field{background:var(--white);font-size:10px;color:#999;padding:8px 12px;letter-spacing:.3px}
.send{left:728px;top:2614px;width:263px;height:35px;background:var(--red);color:var(--white);font-size:11px;font-weight:600;text-align:center;line-height:35px}
.form-note{left:443px;top:2718px;font-family:"Dosis",sans-serif;font-size:11px;color:#777;letter-spacing:.3px}

/* footer */
.footer{left:0;top:2770px;width:1200px;height:60px;background:var(--footer)}
.copyright{left:107px;top:2792px;font-size:11px;color:#dddddd}
.social{top:2786px;width:28px;height:28px;border-radius:50%;background:#777}
</style>
</head>
<body>

<div class="abs hero-photo" role="img" aria-label="Craftsman in a plaid shirt working with wood dust at a workbench"></div>
<header>
  <div class="abs topbar"></div>
  <div class="abs logo">Praxelun</div>
  <div class="abs nav active" style="left:570px">SERVICES</div>
  <div class="abs nav" style="left:670px">ABOUT US</div>
  <div class="abs nav" style="left:776px">CONTACT</div>
  <div class="abs nav-divider" style="left:864px"></div>
  <div class="abs lang">Language:&nbsp; English
    <svg width="10" height="7" viewBox="0 0 10 7"><path d="M1 1l4 4 4-4" stroke="#fff" stroke-width="1.4" fill="none"/></svg>
  </div>
  <div class="abs nav-divider" style="left:1043px"></div>
  <div class="abs social-top" aria-label="Social profile"></div>
</header>
<div class="abs hero-label">WOODWORKS</div>
<div class="abs dots"><span></span><span></span><span></span></div>

<div class="abs quote-band"></div>
<div class="abs quote-text">Are you interested in an estimate?</div>
<div class="abs quote-btn">GET A QUOTE</div>

<h2 class="abs section-title" style="top:815px">OUR SERVICES</h2>

<div class="abs service-photo ph-wood" style="left:100px;top:900px" role="img" aria-label="Hands planing a wooden board"></div>
<svg class="abs" style="left:115px;top:1018px" width="14" height="22" viewBox="0 0 14 22"><path d="M11 2L3 11l8 9" stroke="#fff" stroke-width="2" fill="none"/></svg>
<svg class="abs" style="left:358px;top:1018px" width="14" height="22" viewBox="0 0 14 22"><path d="M3 2l8 9-8 9" stroke="#fff" stroke-width="2" fill="none"/></svg>
<h3 class="abs service-name" style="left:464px;top:892px">WOODWORKS</h3>
<p class="abs service-copy" style="left:466px;top:935px">Praxelun is, in essence, a natural and warm material. Wood is also relatively urable and easy to work with, which has made it a favourite of builders throughout history. Our goal is to offer suitable products and quality furniture with installation and after sales service to all of our clients.In order toachieve this, we're ready to help our clients in all stages of construction from design to</p>
<div class="abs tags" style="left:466px;top:1053px"><span># Furniture</span><span># Windows</span><span># Doors # Staircases</span><span># Woodcarving</span><span># Graining</span></div>
<div class="abs btn btn-red" style="left:468px;top:1111px">View More</div>

<div class="abs rule" style="top:1189px"></div>

<h3 class="abs service-name" style="left:96px;top:1218px">STONEWORKS</h3>
<p class="abs service-copy" style="left:98px;top:1262px;width:640px">The natural stone found in the ground has been used in construction for centuries because of its durability. A structure GALLERY (sliders)built by a skilled craftsman from natural stone is unique, genuine When clicked opensand durable, and perfect for our bracing climate. this category gallery Our experienced craftsmen are ready to help you in all stages of &nbsp;construction from planning to completion.</p>
<div class="abs tags" style="left:98px;top:1387px"><span># Walls</span><span># Terraces</span><span># Paths</span><span># Outdoor kitchens</span><span># Fireplaces</span><span># Smokeries</span><span># Fences</span></div>
<div class="abs btn btn-dark" style="left:100px;top:1436px">View More</div>
<div class="abs service-photo ph-stone" style="left:813px;top:1226px" role="img" aria-label="Natural stone paving slabs laid on gravel"></div>

<div class="abs rule" style="top:1513px"></div>

<div class="abs service-photo ph-restore" style="left:100px;top:1551px" role="img" aria-label="Older craftsman restoring a wooden piece in a workshop"></div>
<h3 class="abs service-name" style="left:464px;top:1545px">RESTORATION</h3>
<p class="abs service-copy" style="left:466px;top:1588px">It's good to see that fixing old things has become popular again in recent years and people are trying to find ways to preserve GALLERY (sliders)valuable old windows and pieces of furniture before deciding to When clicked opensreplace them.this category gallery It is possible to give a new life to almost any wooden door, window, piece of furniture or staircase. The extensive experience of our craftsmen will help you achieve the desired result</p>
<div class="abs tags" style="left:466px;top:1721px"><span># Furniture</span><span># Windows</span><span># Doors# Staircases</span><span># Floors</span><span># Special Projects</span></div>
<div class="abs btn btn-dark" style="left:468px;top:1764px">View More</div>

<section>
  <div class="abs about-band" role="img" aria-label="Darkened workshop backdrop"></div>
  <div class="abs about-photo" role="img" aria-label="Smiling craftsman with ear protection and crossed arms in a workshop"></div>
  <h2 class="abs about-title">ABOUT US</h2>
  <p class="abs about-copy">Praxelun is a company whose business operations include making wooden products, restoration and building structures from natural stone.All of our products are made by raftsmen and specialists who have extensive experience and knowledge in their fields. The products we offer are always handmade and we take the requests and ideas of the specific client into account We always strive to achieve the best possible quality.</p>
  <div class="abs about-sign">Quality matters, <b>Praxelun</b></div>
</section>

<h2 class="abs section-title" style="top:2336px">CONTACT</h2>
<div class="abs contact-sub">PLEASE FILL IN THE FOLLOWING FIELDS IF YOU WOULD LIKE A PRICE QUOTE</div>

<div class="abs info-label" style="top:2488px">CALL ME</div>
<div class="abs info-value" style="top:2508px">TELEPHONE: +372 55 18 302</div>
<div class="abs info-label" style="top:2558px">EMAIL ME</div>
<div class="abs info-value" style="top:2578px">E-MAIL: HELLO@PRAXELUN.EE</div>
<div class="abs info-label" style="top:2630px">ADDRESS</div>
<div class="abs info-value" style="top:2650px">Kalvi 12<br>10415 Harbourtown<br>NORTHLAND</div>

<div class="abs form-panel"></div>
<div class="abs field" style="left:474px;top:2512px;width:226px;height:36px">NAME</div>
<div class="abs field" style="left:474px;top:2564px;width:226px;height:36px">EMAIL</div>
<div class="abs field" style="left:474px;top:2614px;width:226px;height:35px">SUBJECT</div>
<div class="abs field" style="left:728px;top:2512px;width:263px;height:88px">TEXTS</div>
<div class="abs send">SEND NOW</div>
<div class="abs form-note">LOOKING FORWARD TO HEARING FROM YOU!</div>

<footer>
  <div class="abs footer"></div>
  <div class="abs copyright">Copyrights © 2016 yoursite All rights reserved</div>
  <div class="abs social" style="left:975px"></div>
  <div class="abs social" style="left:1011px"></div>
  <div class="abs social" style="left:1047px"></div>
  <div class="abs social" style="left:1083px"></div>
</footer>

</body>
</html>
```